Business Card Design

Business Card for professional consulting firm working with large financial institutions.

Target Market(s)

Executive buyers

Industry/Entity Type

Banking

Contact Information for Business Card

Mild creativity wanted. Not boring, but do elaborate artwork.

Font styles to use
Serif
Sans Serif

Colors

Designer to choose colors to be used in the design.

Requirements
Must have
• Standard business card features - company name, individual name, telephone, website, email, locations.
Nice to have
• Two colors
Should not have
• too many colors, fancy printing, cartoons.

```html
<!DOCTYPE html>
<html lang="en">
<head>
<meta charset="utf-8">
<title>Northvale Business Card</title>
<link rel="stylesheet" href="https://fonts.googleapis.com/css2?family=Merriweather:wght@400&family=Roboto:wght@400&family=Roboto+Condensed:wght@700&display=swap">
<style>
  :root {
    --backdrop: #e9e6e1;
    --card-white: #f4f4f4;
    --band-grey: #aeaeae;
    --band-black: #050505;
    --card-dark: #1b1d20;
    --ink-dark: #141414;
    --ink-mid: #4a4a4a;
    --ink-soft: #a8a8a8;
    --rule: #cfcfcf;
    --logo-grey: #4f4f4f;
    --logo-white: #ffffff;
  }
  * { margin: 0; padding: 0; box-sizing: border-box; }
  html, body { width: 1200px; height: 960px; overflow: hidden; }
  body {
    position: relative;
    background: var(--backdrop);
    font-family: "Roboto", Arial, sans-serif;
  }
  .card {
    position: absolute;
    width: 600px;
    height: 342px;
    box-shadow: 0 4px 10px rgba(0,0,0,0.28);
    overflow: hidden;
  }
  .card--front { left: 314px; top: 114px; background: var(--card-white); }
  .card--back { left: 311px; top: 472px; height: 343px; background: var(--card-dark); }

  .band { position: absolute; left: 0; width: 100%; }
  .band--top { top: 0; height: 17px; background: var(--band-grey); }
  .band--bottom { bottom: 0; height: 18px; background: var(--band-black); }

  .brand-name {
    position: absolute;
    font-family: "Merriweather", Georgia, serif;
    font-weight: 400;
    letter-spacing: 0.5px;
    white-space: nowrap;
  }
  .card--front .brand-name {
    left: 60px; top: 148px;
    font-size: 30px;
    color: var(--logo-grey);
  }
  .card--back .brand-name {
    left: 0; right: 0; top: 143px;
    text-align: center;
    font-size: 34px;
    color: var(--logo-white);
  }

  .divider {
    position: absolute;
    left: 335px; top: 91px;
    width: 1px; height: 163px;
    background: var(--rule);
  }

  .contact { position: absolute; left: 365px; top: 91px; }
  .contact__name {
    font-family: "Roboto Condensed", Arial, sans-serif;
    font-weight: 700;
    font-size: 20px;
    color: var(--ink-dark);
    line-height: 24px;
  }
  .contact__title {
    font-family: "Roboto Condensed", Arial, sans-serif;
    font-weight: 700;
    font-size: 14px;
    color: var(--ink-soft);
    line-height: 18px;
  }
  .contact__address {
    margin-top: 16px;
    font-size: 14px;
    line-height: 18px;
    color: var(--ink-mid);
  }
  .contact__list { list-style: none; margin-top: 10px; }
  .contact__item {
    display: flex; align-items: center;
    font-size: 14px; line-height: 19.5px;
    color: var(--ink-mid);
  }
  .contact__icon { width: 12px; height: 12px; margin-right: 9px; fill: var(--ink-dark); }
</style>
</head>
<body>
  <section class="card card--front" aria-label="Business card front">
    <div class="band band--top"></div>
    <div class="brand-name">northvale</div>
    <div class="divider"></div>
    <div class="contact">
      <div class="contact__name">DANIEL REYES</div>
      <div class="contact__title">CEO/FOUNDER</div>
      <div class="contact__address">4120 Juniper Court<br>Fairbanks, Alaska 34810</div>
      <ul class="contact__list">
        <li class="contact__item">
          <svg class="contact__icon" viewBox="0 0 24 24" aria-hidden="true"><path d="M6.6 10.8c1.4 2.8 3.8 5.1 6.6 6.6l2.2-2.2c.3-.3.7-.4 1-.2 1.1.4 2.3.6 3.6.6.6 0 1 .4 1 1V20c0 .6-.4 1-1 1C10.6 21 3 13.4 3 4c0-.6.4-1 1-1h3.5c.6 0 1 .4 1 1 0 1.3.2 2.5.6 3.6.1.3 0 .7-.2 1L6.6 10.8z"/></svg>
          512 604 1187
        </li>
        <li class="contact__item">
          <svg class="contact__icon" viewBox="0 0 24 24" aria-hidden="true"><path d="M2 5h20v14H2z M4 7v.5l8 5 8-5V7z" fill-rule="evenodd"/></svg>
          info@northvale.com
        </li>
        <li class="contact__item">
          <svg class="contact__icon" viewBox="0 0 24 24" aria-hidden="true"><circle cx="12" cy="12" r="10"/><path d="M7 8c2 0 3 1 3 3s-2 2-2 4M14 5c0 2 2 2 3 3s0 3 2 4" stroke="#f4f4f4" stroke-width="2" fill="none"/></svg>
          www.northvale.com
        </li>
      </ul>
    </div>
    <div class="band band--bottom"></div>
  </section>

  <section class="card card--back" aria-label="Business card back">
    <div class="brand-name">northvale</div>
  </section>
</body>
</html>
```